Gutschein-Design für Verkauf von Online-Schmuckstücken
Zielgruppe
Wir verkaufen Online Schmuckstücke!
www.silberfaden-shop.de
Aufgabenstellung
Wir haben eine schwarze Schachtel erstellt und da drinne wird eine Geschenkgutschein sein:
Es soll sehr schlicht sein und schwarzen Hintergrund haben.
Vorderseite nur unser LOGO.
Rückseite:
Betrag: _________
Gültig Bis: _________
Code: __________
Und unten klein gedruckt steht:
Diese Karte ist gültig nur auf der online shop seite www.silberfaden-shop.de und in unserer offizielen Stores. Dieses Karte ist nicht gültig bei rabatierte Produkten und man kann nicht mit dieser karte einen Gutscheinkarte kaufen.
Der Design soll sehr schlicht und dezenz sein.

```html
<!DOCTYPE html>
<html lang="de">
<head>
<meta charset="utf-8">
<title>Silberfaden Geschenkgutschein</title>
<link rel="stylesheet" href="https://fonts.googleapis.com/css2?family=Cormorant+Garamond:wght@400;500&display=swap">
<style>
  :root {
    --paper: #ffffff;
    --ink: #141414;
    --night: #000000;
    --rose: #e597ae;
    --rose-soft: #f1b9c6;
    --mauve: #7d4c5c;
    --leaf: #4a5552;
  }
  html, body {
    margin: 0;
    padding: 0;
    width: 1200px;
    height: 851px;
    overflow: hidden;
    background: var(--paper);
  }
  .canvas {
    position: relative;
    width: 1200px;
    height: 851px;
    overflow: hidden;
  }
  .card {
    position: absolute;
    top: 0;
    left: 0;
    width: 851px;
    height: 1200px;
    transform-origin: 0 0;
    transform: translate(0, 851px) rotate(-90deg);
    font-family: "Cormorant Garamond", Georgia, serif;
  }
  .front {
    position: absolute;
    left: 0; top: 0;
    width: 851px; height: 591px;
    background: var(--paper);
  }
  .brand-dot {
    position: absolute;
    left: 291px; top: 103px;
    width: 234px; height: 234px;
    border-radius: 50%;
    background: var(--ink);
  }
  .brand-name {
    position: absolute;
    left: 0; top: 335px;
    width: 851px;
    text-align: center;
    font-size: 150px;
    font-weight: 500;
    line-height: 1;
    color: var(--ink);
    letter-spacing: 2px;
  }
  .back {
    position: absolute;
    left: 0; top: 591px;
    width: 851px; height: 609px;
    background: var(--night);
    overflow: hidden;
  }
  .floral {
    position: absolute;
    width: 178px;
    height: 576px;
    top: 0;
  }
  .floral--top-edge {
    right: 0;
    background:
      radial-gradient(ellipse 90px 120px at 60% 42%, rgba(241,175,190,0.95), rgba(241,175,190,0) 100%),
      radial-gradient(ellipse 80px 110px at 55% 78%, rgba(232,150,170,0.9), rgba(232,150,170,0) 100%),
      linear-gradient(90deg, rgba(74,85,82,0) 0%, rgba(74,85,82,0.55) 100%);
  }
  .floral--bottom-edge {
    left: 0;
    background:
      radial-gradient(ellipse 90px 120px at 40% 22%, rgba(241,175,190,0.95), rgba(241,175,190,0) 100%),
      radial-gradient(ellipse 80px 110px at 45% 62%, rgba(232,150,170,0.9), rgba(232,150,170,0) 100%),
      linear-gradient(270deg, rgba(74,85,82,0) 0%, rgba(74,85,82,0.55) 100%);
  }
  .field {
    position: absolute;
    left: 0;
    width: 851px;
    height: 60px;
  }
  .field__label {
    position: absolute;
    right: 429px;
    bottom: 0;
    font-size: 44px;
    line-height: 1;
    font-variant: small-caps;
    color: var(--rose);
    white-space: nowrap;
  }
  .field__line {
    position: absolute;
    left: 429px;
    bottom: 2px;
    width: 152px;
    height: 2px;
    background: var(--rose);
  }
  .field--amount { top: 145px; }
  .field--valid  { top: 265px; }
  .field--code   { top: 386px; }
  .terms {
    position: absolute;
    left: 0;
    top: 573px;
    width: 851px;
    height: 27px;
    background: var(--mauve);
    display: flex;
    flex-direction: column;
    justify-content: center;
    align-items: center;
    color: var(--rose-soft);
    font-size: 7.6px;
    line-height: 1.25;
    font-variant: small-caps;
    letter-spacing: 0.2px;
  }
  .terms p { margin: 0; }
</style>
</head>
<body>
<div class="canvas">
  <div class="card">
    <section class="front">
      <div class="brand-dot"></div>
      <div class="brand-name">Silberfaden</div>
    </section>
    <section class="back">
      <div class="floral floral--top-edge" role="img" aria-label="Aquarell-Blumen in Rosa mit grauen Blättern"></div>
      <div class="floral floral--bottom-edge" role="img" aria-label="Aquarell-Blumen in Rosa mit grauen Blättern"></div>

      <div class="field field--amount">
        <span class="field__label">Betrag:</span>
        <span class="field__line"></span>
      </div>
      <div class="field field--valid">
        <span class="field__label">Gültig bis:</span>
        <span class="field__line"></span>
      </div>
      <div class="field field--code">
        <span class="field__label">Code:</span>
        <span class="field__line"></span>
      </div>

      <div class="terms">
        <p>Diese Karte ist nur auf der Online Shop Seite www.silberfaden-shop.de und in unseren offiziellen Stores gültig.</p>
        <p>Diese Karte ist bei rabattierte Produkten nicht gültig und man kann mit dieser Karte keine Gutscheinkarte kaufen.</p>
      </div>
    </section>
  </div>
</div>
</body>
</html>
```